Tallowmere Air Business Card Design

Design new, 2 sides, business cards for a residential and light commercial heating, air conditioning contractor.

Target Market(s)

Homeowners, small businesses

Industry/Entity Type

Business

Contact Information for Business Card

Dominic Westerhall
Phone - 862-415-2736
Email
Address - PO box 518
Brightwater NJ 07912
Website - www.HarborBreezeLLC.example

Requirements
Must have
• logo, company colors, standard size with no die cut, so I can use nova stamp

```html
<!DOCTYPE html>
<html lang="en">
<head>
<meta charset="utf-8">
<title>Tallowmere Air Business Card</title>
<link href="https://fonts.googleapis.com/css2?family=Open+Sans:wght@400;600;700&display=swap" rel="stylesheet">
<style>
  :root {
    --maroon: #9c1f33;
    --maroon-deep: #8e1c2e;
    --orange: #f5872f;
    --cream: #fbe8b4;
    --white: #ffffff;
    --backdrop: #ecebe8;
  }
  * { margin: 0; padding: 0; box-sizing: border-box; }
  html, body {
    width: 1200px; height: 900px; overflow: hidden;
    background: var(--backdrop);
    font-family: "Open Sans", Arial, sans-serif;
  }
  .card {
    position: absolute;
    overflow: hidden;
    box-shadow: 0 4px 14px rgba(0,0,0,0.18);
  }
  .card-front {
    left: 238px; top: 62px; width: 556px; height: 342px;
    background: var(--maroon);
  }
  .card-back {
    left: 458px; top: 518px; width: 560px; height: 343px;
  }
  .accent-panel { position: absolute; inset: 0; }
  .holder {
    position: absolute; left: 35px; top: 31px; color: var(--white);
  }
  .holder-name {
    color: var(--orange); font-weight: 700; font-size: 17px; letter-spacing: 0.3px;
  }
  .holder-role { font-size: 16px; margin-top: 2px; }
  .contact-list {
    position: absolute; left: 35px; list-style: none; color: var(--white);
    font-size: 15.5px; line-height: 21px;
  }
  .contact-phones { top: 204px; }
  .contact-online { top: 268px; }
  .contact-list li { display: flex; align-items: center; gap: 5px; }
  .contact-list svg { width: 11px; height: 11px; fill: var(--orange); }
  .address {
    position: absolute; right: 30px; top: 270px; text-align: right;
    color: var(--white); font-size: 15px; line-height: 22px; font-style: normal;
  }
  .brand-mark {
    position: absolute; display: flex; align-items: center; justify-content: center; gap: 12px;
    color: var(--cream); font-weight: 700; white-space: nowrap;
  }
  .card-front .brand-mark { left: 180px; top: 108px; width: 340px; font-size: 36px; }
  .card-back .brand-mark { left: 0; top: 138px; width: 560px; font-size: 48px; }
  .brand-dot { border-radius: 50%; background: var(--cream); flex: none; }
  .card-front .brand-dot { width: 22px; height: 22px; }
  .card-back .brand-dot { width: 28px; height: 28px; }
  .back-surface {
    position: absolute; inset: 0;
    background: radial-gradient(ellipse at center, var(--maroon) 0%, var(--maroon-deep) 100%);
  }
</style>
</head>
<body>
  <section class="card card-front">
    <svg class="accent-panel" viewBox="0 0 556 342" preserveAspectRatio="none" aria-hidden="true">
      <polygon points="497,0 556,0 556,342 290,342" fill="var(--orange)"/>
    </svg>
    <div class="holder">
      <p class="holder-name">DOMINIC WESTERHALL</p>
      <p class="holder-role">Director</p>
    </div>
    <div class="brand-mark"><span class="brand-dot"></span>Tallowmere Air</div>
    <ul class="contact-list contact-phones">
      <li><svg viewBox="0 0 12 12"><path d="M1 4c0-2 2-3 5-3s5 1 5 3l-2 1-1-1.5H4L3 5zM2 6h8l1 5H1z"/></svg>862-415-2736</li>
      <li><svg viewBox="0 0 12 12"><path d="M3 1h6v3H3zM1 4h10v7H1zM4 6v3h4V6z"/></svg>862-415-2790</li>
    </ul>
    <ul class="contact-list contact-online">
      <li><svg viewBox="0 0 12 12"><path d="M0 2h12v1L6 7 0 3zM0 4.5l6 4 6-4V10H0z"/></svg>info@tallowmere.example</li>
      <li><svg viewBox="0 0 12 12"><circle cx="6" cy="6" r="5.5"/></svg>www.TallowmereLLC.example</li>
    </ul>
    <address class="address">
      PO box 518<br>Brightwater NJ 07912
    </address>
  </section>

  <section class="card card-back">
    <div class="back-surface" role="img" aria-label="Embossed crinkled maroon paper texture"></div>
    <div class="brand-mark"><span class="brand-dot"></span>Tallowmere Air</div>
  </section>
</body>
</html>
```